Stationery Design Task - Stationary, memo and report templates for professional services company

Looking for someone to update stationary design but just as importantly come up with a template for reports and memos for use in our consulting firm. Would also like some brand use guidelines to be able to share with our whole team. We have an existing logo that we like. Need to update with a more contemporary look so that our deliverables to clients look good and professional yet stylish. This is for business to business communications. No need for envelope design. Important to have design for multiple pages, i.e. first page of a report and then 2nd page. Need to use in MS word documents so must be easy to use and replicate. Don't want something overly complex. Clean, fresh looking is best.

Industry/Entity Type

Information Technology

Font styles to use
Sans Serif

Colors
33a6d7
0792cd
85cae6
cee9f5
cedeed
85abd2
3377b5
0455a3

Requirements
Must have
• Clean look but with a little style or pop. Something that can easily be used in word documents. Need to have page styles that have a first page of a report (not a cover page) and then secondary page.
Nice to have
• - Although the dark blue is our primary color. Might be willing to look at some accent color as well.
Should not have
• Not just our logo on the page with a color bar.

```html
<!DOCTYPE html>
<html lang="en">
<head>
<meta charset="utf-8">
<title>Corvale Systems – Stationery Set</title>
<link rel="stylesheet" href="https://fonts.googleapis.com/css2?family=Montserrat:wght@600;700;800&family=Questrial&display=swap">
<style>
  :root {
    --stage: #676767;
    --brand-blue: #0b6fbf;
    --brand-dark: #0455a3;
    --brand-mid: #0792cd;
    --text-grey: #4a4a4a;
    --body-grey: #6b6b6b;
    --rule-grey: #8c8c8c;
    --tab-grey: #8f8f8f;
    --paper-top: #f4f4f4;
    --paper-bottom: #c9c9c9;
    --white: #ffffff;
  }
  * { margin: 0; padding: 0; box-sizing: border-box; }
  html, body { width: 1200px; height: 578px; overflow: hidden; }
  body {
    background: var(--stage);
    position: relative;
    font-family: "Questrial", "Century Gothic", sans-serif;
    color: var(--text-grey);
  }

  .page {
    position: absolute;
    top: 53px;
    width: 338px;
    height: 474px;
    background: linear-gradient(180deg, var(--paper-top) 0%, #e4e4e4 55%, var(--paper-bottom) 100%);
    box-shadow: 0 0 3px rgba(0,0,0,0.25);
    overflow: hidden;
  }
  .page--cover { left: 62px; }
  .page--letter { left: 434px; }
  .page--continuation {
    left: 807px;
    background: linear-gradient(90deg, #e9e9e9 0%, #fbfbfb 40%, #f2f2f2 60%, #e6e6e6 100%);
  }

  .brand-mark {
    position: absolute;
    display: flex;
    align-items: center;
    gap: 8px;
  }
  .brand-mark__dot {
    border-radius: 50%;
    background: var(--brand-mid);
    flex: none;
  }
  .brand-mark__name {
    font-family: "Montserrat", sans-serif;
    font-weight: 800;
    color: var(--brand-blue);
    line-height: 1;
    letter-spacing: 0.5px;
  }

  /* Cover */
  .cover__brand { left: 36px; top: 50px; }
  .cover__brand .brand-mark__dot { width: 36px; height: 36px; }
  .cover__brand .brand-mark__name { font-size: 19px; line-height: 1.05; }

  .cover__band { position: absolute; left: 0; top: 0; width: 338px; height: 474px; }

  .cover__title {
    position: absolute;
    left: 35px; top: 128px;
    font-family: "Montserrat", sans-serif;
    font-weight: 800;
    font-size: 31px;
    line-height: 30px;
    color: var(--brand-blue);
    letter-spacing: 1px;
  }
  .cover__subtitle {
    position: absolute;
    left: 39px; top: 191px;
    font-family: "Montserrat", sans-serif;
    font-weight: 700;
    font-size: 11.5px;
    color: var(--text-grey);
  }
  .cover__byline-label {
    position: absolute;
    left: 40px; top: 222px;
    font-family: "Montserrat", sans-serif;
    font-weight: 700;
    font-size: 10.5px;
    color: var(--brand-blue);
  }
  .cover__byline-name {
    position: absolute;
    left: 40px; top: 238px;
    font-family: "Montserrat", sans-serif;
    font-weight: 600;
    font-size: 9.5px;
    color: var(--text-grey);
  }
  .cover__dates {
    position: absolute;
    left: 184px; top: 376px;
    width: 94px;
    color: var(--white);
    font-family: "Montserrat", sans-serif;
    font-weight: 600;
    font-size: 8.5px;
    line-height: 11.5px;
  }
  .cover__dates hr {
    border: 0;
    border-top: 1px solid var(--white);
    margin: 7px 0 8px;
  }

  /* Letterhead */
  .letter__symbol { position: absolute; left: 31px; top: 24px; width: 38px; height: 38px; border-radius: 50%; background: var(--brand-mid); }
  .letter__brand {
    position: absolute;
    right: 29px; top: 27px;
    text-align: right;
  }
  .letter__brand-name {
    font-family: "Montserrat", sans-serif;
    font-weight: 800;
    font-size: 13px;
    color: var(--brand-blue);
    line-height: 1.05;
  }
  .letter__contact {
    margin-top: 5px;
    font-size: 5.6px;
    line-height: 9px;
    color: var(--text-grey);
    letter-spacing: 0.1px;
  }
  .letter__body {
    position: absolute;
    left: 30px; top: 133px;
    width: 282px;
  }
  .letter__salutation { font-size: 8.5px; color: var(--text-grey); margin-bottom: 12px; }
  .letter__body p.copy {
    font-size: 4.6px;
    line-height: 7.2px;
    color: var(--body-grey);
    text-align: justify;
    margin-bottom: 7px;
  }
  .letter__closing { font-size: 4.6px; color: var(--body-grey); margin-top: 10px; }
  .letter__signature {
    display: block;
    margin-top: 10px;
    width: 62px; height: 28px;
    border-radius: 3px;
    background: linear-gradient(90deg, rgba(133,171,210,0.45), rgba(206,222,237,0.35));
  }

  .page--continuation .continuation__brand { left: 29px; top: 26px; }
  .page--continuation .brand-mark__dot { width: 34px; height: 34px; }
  .page--continuation .brand-mark__name { font-size: 10px; }

  /* Shared footer */
  .page-footer { position: absolute; left: 30px; top: 438px; width: 279px; height: 14px; }
  .page-footer__rule { position: absolute; left: 0; top: 0; width: 100%; border-top: 0.8px solid var(--rule-grey); }
  .page-footer__url {
    position: absolute; left: 0; top: 6px;
    font-family: "Montserrat", sans-serif;
    font-weight: 600;
    font-size: 5.6px;
    color: var(--brand-mid);
  }
  .page-footer__tab {
    position: absolute; right: 0; top: 2px;
    width: 34px; height: 11px;
    background: var(--tab-grey);
    clip-path: polygon(4px 0, 100% 0, 100% 100%, 0 100%, 0 4px);
    color: var(--white);
    font-family: "Montserrat", sans-serif;
    font-weight: 700;
    font-size: 5px;
    line-height: 11px;
    text-align: center;
  }
</style>
</head>
<body>

  <!-- Report first page -->
  <section class="page page--cover">
    <svg class="cover__band" viewBox="0 0 338 474" role="img" aria-label="Blue diagonal band with a soft honeycomb texture">
      <defs>
        <linearGradient id="bandFill" x1="0" y1="0" x2="0.4" y2="1">
          <stop offset="0" stop-color="#2a8ed6"/>
          <stop offset="0.5" stop-color="#0b72c2"/>
          <stop offset="1" stop-color="#0a5ea8"/>
        </linearGradient>
      </defs>
      <polygon points="330,36 330,466 91,466" fill="url(#bandFill)"/>
    </svg>

    <div class="brand-mark cover__brand">
      <span class="brand-mark__dot"></span>
      <span class="brand-mark__name">CORVALE<br>SYSTEMS</span>
    </div>

    <h1 class="cover__title">REPORT<br>TITLE HERE</h1>
    <p class="cover__subtitle">YOUR SUBTITLE HERE</p>
    <p class="cover__byline-label">REPORT PREPARED BY</p>
    <p class="cover__byline-name">YOUR NAME HERE</p>

    <div class="cover__dates">
      <p>PROPOSAL ISSUED<br>SEP 19,2018</p>
      <hr>
      <p>PROPOSAL VALID TO<br>SEP 19,2019</p>
    </div>
  </section>

  <!-- Letterhead -->
  <section class="page page--letter">
    <span class="letter__symbol"></span>
    <div class="letter__brand">
      <p class="letter__brand-name">CORVALE SYSTEMS</p>
      <p class="letter__contact">1420 HARBOR VIEW ROAD, JUNEAU, ALASKA 99801<br>555 210 4417 | INFO@CORVALESYSTEMS.COM</p>
    </div>

    <div class="letter__body">
      <p class="letter__salutation">Dear Mr. Harlow,</p>
      <p class="copy">Thank you for meeting with our team last week to discuss the upcoming network refresh. We have reviewed the notes from the session and prepared an outline of the next steps for your office. Our engineers will begin with a full audit of the current servers, switches and storage, then share a short summary of findings with your staff before any changes are planned.</p>
      <p class="copy">The audit will take about two weeks and can be scheduled outside of business hours to avoid any disruption. Once it is complete, we will meet again to agree on priorities, budget and timing. Our proposal covers hardware, licensing, backup and support, and each item can be adjusted to suit your needs.</p>
      <p class="copy">During the project a dedicated consultant will be your single point of contact. You will receive a brief weekly report showing progress, open questions and any risks we have found. All work is carried out by certified staff and follows the security standards agreed with your team at the start of the project. We also provide training sessions so that your own staff feel confident with every new system.</p>
      <p class="copy">Please review the attached proposal and let us know if you have any questions. We would be glad to arrange a call at a time that suits you, and we look forward to working with your team on this project.</p>
      <p class="letter__closing">Sincerely,</p>
      <span class="letter__signature" role="img" aria-label="Handwritten signature of Daniel Harlow"></span>
    </div>

    <footer class="page-footer">
      <span class="page-footer__rule"></span>
      <span class="page-footer__url">WWW.CORVALESYSTEMS.COM</span>
      <span class="page-footer__tab">PAGE 1</span>
    </footer>
  </section>

  <!-- Continuation page -->
  <section class="page page--continuation">
    <div class="brand-mark continuation__brand">
      <span class="brand-mark__dot"></span>
      <span class="brand-mark__name">CORVALE</span>
    </div>

    <footer class="page-footer">
      <span class="page-footer__rule"></span>
      <span class="page-footer__url">WWW.CORVALESYSTEMS.COM</span>
      <span class="page-footer__tab">PAGE 1</span>
    </footer>
  </section>

</body>
</html>
```